Brightmoor Essentials colloidal silver spray for pets.

We need a label for an 8-oz cobalt blue spray bottle. We are a small company just starting to share the benefits of colloidal silver. Our first offering will be the 8-oz spray bottle for pets. We would also like to update our logo. The finished project should be crisp and incorporate a dog on the label. I have attached the information we would like on the label and our logo, which can be changed to match your vision.
Updates

Hi, I would like to remind you that we are using a cobalt blue bottle with a black sprayer and would like an updated logo. Also, for the business cards, we don't want an animal on them, as we are planning future products for people. thank you

```html
<!DOCTYPE html>
<html lang="en">
<head>
<meta charset="utf-8">
<title>Colloidal Silver – Natural First Aid for Pets</title>
<link rel="stylesheet" href="https://fonts.googleapis.com/css2?family=Roboto+Condensed:wght@700&family=Arimo:wght@400&display=swap">
<style>
  :root {
    --page: #ffffff;
    --label-dark: #9d9d9d;
    --label-light: #e4e4e4;
    --label-mid: #b9b9b9;
    --title-blue: #2b3391;
    --text-dark: #2f2f2f;
    --text-body: #2a2a2a;
    --tick-green: #1d9a45;
    --tick-red: #d0312d;
    --pet-light: #d88a3c;
    --pet-mid: #b0601f;
    --pet-dark: #6e3510;
    --badge-fill: #f4f4f4;
    --badge-ring: #c9c9c9;
    --badge-red: #d52b1e;
  }
  * { margin: 0; padding: 0; box-sizing: border-box; }
  html, body {
    width: 1200px;
    height: 1200px;
    overflow: hidden;
    background: var(--page);
  }
  .canvas {
    position: relative;
    width: 1200px;
    height: 1200px;
    background: var(--page);
  }
  .label {
    position: absolute;
    left: 358px;
    top: 40px;
    width: 484px;
    height: 1120px;
    overflow: hidden;
    background: linear-gradient(90deg,
      var(--label-dark) 0%,
      var(--label-mid) 22%,
      var(--label-light) 55%,
      var(--label-mid) 85%,
      #a9a9a9 100%);
  }
  .label__title {
    position: absolute;
    left: 0;
    top: 0;
    width: 484px;
    height: 360px;
  }
  .label__title text {
    font-family: "Roboto Condensed", sans-serif;
    font-weight: 700;
    fill: var(--title-blue);
  }
  .label__tagline {
    position: absolute;
    left: 0;
    width: 476px;
    text-align: center;
    font-family: "Roboto Condensed", sans-serif;
    font-weight: 700;
    font-size: 40px;
    line-height: 1;
    color: var(--text-dark);
  }
  .label__tagline--top { top: 398px; }
  .label__tagline--bottom { top: 448px; }
  .label__specs {
    position: absolute;
    left: 0;
    top: 496px;
    width: 484px;
    font-family: "Arimo", sans-serif;
    font-size: 19px;
    color: var(--text-body);
  }
  .spec-row {
    position: relative;
    height: 24px;
  }
  .spec-row__left {
    position: absolute;
    right: 290px;
    top: 0;
    white-space: nowrap;
  }
  .spec-row__tick {
    position: absolute;
    left: 200px;
    top: 1px;
    width: 22px;
    height: 22px;
  }
  .spec-row__right {
    position: absolute;
    left: 230px;
    top: 0;
    white-space: nowrap;
  }
  .label__pet-photo {
    position: absolute;
    left: 0;
    top: 588px;
    width: 280px;
    height: 532px;
    border-radius: 48% 52% 0 0 / 18% 20% 0 0;
    background: radial-gradient(ellipse at 45% 35%,
      var(--pet-light) 0%,
      var(--pet-mid) 55%,
      var(--pet-dark) 100%);
  }
  .label__origin-badge {
    position: absolute;
    left: 372px;
    top: 722px;
    width: 62px;
    height: 62px;
  }
  .label__claims {
    position: absolute;
    right: 35px;
    top: 800px;
    text-align: right;
    font-family: "Arimo", sans-serif;
    font-size: 20px;
    line-height: 25px;
    color: var(--text-body);
  }
  .label__net {
    position: absolute;
    left: 292px;
    top: 1080px;
    font-family: "Arimo", sans-serif;
    font-size: 17px;
    color: var(--text-body);
    transform: rotate(-2deg);
    transform-origin: left center;
  }
</style>
</head>
<body>
<main class="canvas">
  <section class="label">

    <svg class="label__title" viewBox="0 0 484 360" role="heading" aria-level="1" aria-label="Colloidal Silver">
      <text x="108" y="209" font-size="120" textLength="356" lengthAdjust="spacingAndGlyphs">COLLOIDAL</text>
      <text x="140" y="339" font-size="120" textLength="280" lengthAdjust="spacingAndGlyphs">SILVER</text>
    </svg>

    <p class="label__tagline label__tagline--top">NATURAL FIRST AID</p>
    <p class="label__tagline label__tagline--bottom">FOR PETS</p>

    <div class="label__specs">
      <div class="spec-row">
        <span class="spec-row__left">10 PPM</span>
        <svg class="spec-row__tick" viewBox="0 0 22 22" aria-hidden="true">
          <circle cx="11" cy="11" r="9" fill="var(--tick-green)"/>
          <path d="M5 11 L10 16 L19 3" fill="none" stroke="var(--tick-red)" stroke-width="2.4" stroke-linecap="round" stroke-linejoin="round"/>
        </svg>
        <span class="spec-row__right">No preservatives</span>
      </div>
      <div class="spec-row">
        <span class="spec-row__left">100% pure</span>
        <svg class="spec-row__tick" viewBox="0 0 22 22" aria-hidden="true">
          <circle cx="11" cy="11" r="9" fill="var(--tick-green)"/>
          <path d="M5 11 L10 16 L19 3" fill="none" stroke="var(--tick-red)" stroke-width="2.4" stroke-linecap="round" stroke-linejoin="round"/>
        </svg>
        <span class="spec-row__right">No additives</span>
      </div>
    </div>

    <div class="label__pet-photo" role="img" aria-label="Photo of a smiling orange Pomeranian dog sitting"></div>

    <svg class="label__origin-badge" viewBox="0 0 62 62" role="img" aria-label="Country of origin badge">
      <circle cx="31" cy="31" r="29" fill="var(--badge-fill)" stroke="var(--badge-ring)" stroke-width="2"/>
    </svg>

    <p class="label__claims">
      Anti microbial,<br>
      Anti Fungal,<br>
      Anti Bacterial,<br>
      Anti Viral<br>
      Treats burns,<br>
      bites,<br>
      cuts,<br>
      abrasions,<br>
      hots spots
    </p>

    <p class="label__net">Net Wight 8 oz</p>

  </section>
</main>
</body>
</html>
```